Marava Cove Lodge Christmas wishes 2013

We require postcards designed to mail our to our clients for Christmas. We are a SURF travel company, with a high end market and like to mail our Christmas postcards to all our guests that have stayed with us through the year. Front cover will have images and text (ie Seasons Greeting) and our logo. The back will have space for TO: name & address and postage stamp. Will also have some basic text (ie The Management & Staff at Marava Cove Lodge wish you and your family all the best for the Festive Season and New Year. We look forward to seeing you back at Marava Cove Lodge again soon etc etc). Here is link to main image https://www.filecrate-example.com/sh/qwmxrtz481plo/Vb7kRtPwqN

Target Market(s)

Our clients are mostly mature men (40-70) surfers who purchase luxury surf trips

Industry/Entity Type

Travel

Requirements
Must have
• Ocean Image (front)
Logo x 2 in same colour - Orindel & Marava Cove Lodge (front)
Text (front)
Back to be white
Space for name & address (back)
Space for postage stamp (back)
Message (back)
Website www.orindellodges-example.com (back)

```html
<!DOCTYPE html>
<html lang="en">
<head>
<meta charset="utf-8">
<title>Marava Cove Lodge – Season's Greetings Postcard</title>
<link href="https://fonts.googleapis.com/css2?family=Questrial&family=Libre+Baskerville:wght@700&display=swap" rel="stylesheet">
<style>
  :root {
    --ink-blue: #4f7fc4;
    --line-blue: #5b85c6;
    --paper: #ffffff;
    --navy-deep: #081f3d;
    --navy-bright: #0d4f9c;
    --sky: #2f7fd6;
    --sea-light: #1f8ed0;
    --sea-deep: #0a4f98;
    --white: #ffffff;
  }
  * { margin: 0; padding: 0; box-sizing: border-box; }
  html, body { width: 891px; height: 1200px; overflow: hidden; background: var(--paper); }
  .postcard {
    position: relative; width: 891px; height: 1200px; overflow: hidden;
    background: var(--paper); font-family: "Questrial", "Helvetica Neue", Arial, sans-serif;
  }
  .site-url {
    position: absolute; left: 27px; top: 21px;
    font-size: 18px; color: var(--ink-blue); letter-spacing: 0.2px;
  }
  .stamp-box {
    position: absolute; left: 752px; top: 37px; width: 102px; height: 127px;
    border: 1.5px solid var(--line-blue);
  }
  .address-lines { position: absolute; left: 277px; top: 137px; width: 361px; }
  .address-lines span {
    display: block; height: 1.5px; background: var(--line-blue); margin-bottom: 35px;
  }
  .message {
    position: absolute; left: 244px; top: 390px; width: 440px;
    text-align: center; font-size: 18.5px; line-height: 25.5px; color: var(--ink-blue);
  }
  .quote-mark {
    position: absolute; font-family: "Libre Baskerville", Georgia, serif; font-weight: 700;
    font-size: 78px; line-height: 1; color: var(--ink-blue);
  }
  .quote-open { left: 226px; top: 360px; }
  .quote-close { left: 601px; top: 497px; }
  .front-band {
    position: absolute; left: 0; top: 607px; width: 891px; height: 593px;
    background: linear-gradient(100deg, var(--navy-deep) 0%, #0b3466 45%, var(--navy-bright) 100%);
  }
  .greeting {
    position: absolute; left: 0; right: 0; top: 606px; text-align: center;
    font-size: 38px; color: var(--white); letter-spacing: 0.3px;
    text-shadow: 0 1px 3px rgba(0,0,0,0.45);
  }
  .ocean-photo {
    position: absolute; left: 85px; top: 655px; width: 710px; height: 475px;
    background: linear-gradient(180deg, var(--sky) 0%, #6aa9e6 14%, #9fc6ec 24%, #1b6fc4 26%,
      var(--sea-light) 45%, #0c62ad 70%, var(--sea-deep) 100%);
  }
  .brand-footer {
    position: absolute; left: 88px; top: 1150px; display: flex; align-items: center; gap: 12px;
    color: var(--white); font-size: 13px; letter-spacing: 1.6px;
  }
  .brand-dot { width: 14px; height: 14px; border-radius: 50%; background: var(--white); }
  .lodge-mark {
    position: absolute; right: 96px; top: 1133px; text-align: center; color: var(--white);
  }
  .lodge-name { font-size: 15px; letter-spacing: 0.5px; }
  .lodge-url { font-size: 12px; margin-top: 4px; }
  .lodge-country { font-size: 9.5px; letter-spacing: 1.4px; margin-top: 1px; }
</style>
</head>
<body>
<main class="postcard">
  <section class="back-side">
    <p class="site-url">www.orindellodges-example.com</p>
    <div class="stamp-box" aria-label="Postage stamp area"></div>
    <div class="address-lines" aria-label="Address lines"><span></span><span></span><span></span><span></span></div>
    <span class="quote-mark quote-open">“</span>
    <p class="message">The Management &amp; Staff at Marava Cove Lodge<br>wish you and your family all the best<br>for the Festive Season and New Year.<br>We look forward to seeing you back at<br>Marava Cove Lodge again soon…</p>
    <span class="quote-mark quote-close">”</span>
  </section>
  <section class="front-band">
  </section>
  <h1 class="greeting">Season's Greetings</h1>
  <div class="ocean-photo" role="img" aria-label="Photo of a clear turquoise lagoon under a bright sky with clouds, a surfer riding a distant wave and a swimmer in the foreground"></div>
  <div class="brand-footer"><span class="brand-dot"></span><span>ORINDEL LODGES &amp; RESORTS</span></div>
  <div class="lodge-mark">
    <div class="lodge-name">Marava Cove Lodge</div>
    <div class="lodge-url">maravacovelodge-example.com</div>
    <div class="lodge-country">indonesia</div>
  </div>
</main>
</body>
</html>
```